we can communicate on this, but i want to follow the approach we took on Pellew|Marsh & Quinlan but i feel the card front needs the black background and the platinum and gold logo. The back? I am open. we can use the same info from PM&Q. Velmont Arc is an enhanced equity investment fund - basically a very exclusive boutique hedge fund that uses only stock options. very advanced things. hope you are interested

Contact Information for Business Card

Dr. Lewis T. Brennick, CFA
Scientifique de fusée financière
701.555.0143
LTBquant47@mailvantor.com

4718 Willow Creek Bend W.
West Fargo, ND 58078

No web site

Colors

Designer to choose colors to be used in the design.

Requirements
Nice to have
• I tend to prefer the most visible applications of the logo to include logo and name, the logo version with a black background and the gold and platinum components separated by the black. I see this working well for a single side (logo and name - this is card front to me).
• I am fairly open to other treatments on the reverse side with the data. To me, it makes sense to have a different color rendition of the logo on the reverse and it may be a muted black tone on tone or an oversized portion that would have spot UV. Or, the reverse may play with colors and layout
Should not have
• Other colors = no no
• Decorative font

```html
<!DOCTYPE html>
<html lang="en">
<head>
<meta charset="utf-8">
<title>Velmont Arc — Business Card</title>
<link rel="stylesheet" href="https://fonts.googleapis.com/css2?family=Montserrat:wght@300;700&family=Roboto:wght@400&family=Saira+Semi+Condensed:wght@600&display=swap">
<style>
  :root {
    --backdrop: #3a3a3b;
    --card: #1c1c1d;
    --card-soft: #222223;
    --gold: #d4a92a;
    --gold-deep: #8a6a12;
    --white: #f4f4f4;
    --platinum: #b9b9bb;
    --faint: #2a2a2b;
  }
  * { margin: 0; padding: 0; box-sizing: border-box; }
  html, body { width: 799px; height: 1200px; overflow: hidden; }
  body {
    background: var(--backdrop);
    position: relative;
    font-family: "Roboto", Arial, sans-serif;
  }
  .card {
    position: absolute;
    left: 80px;
    width: 640px;
    height: 366px;
    background: var(--card);
    border-radius: 3px;
    overflow: hidden;
  }
  .card--front { top: 100px; }
  .card--back { top: 680px; background: var(--card-soft); }

  /* Front */
  .front-lockup {
    position: absolute;
    inset: 0;
    display: flex;
    flex-direction: column;
    align-items: center;
    justify-content: center;
    gap: 26px;
  }
  .brand-dot {
    width: 104px; height: 104px;
    border-radius: 50%;
    background: var(--gold);
  }
  .brand-name {
    font-family: "Montserrat", Arial, sans-serif;
    font-weight: 700;
    color: var(--white);
    font-size: 52px;
    letter-spacing: 1px;
    line-height: 1;
  }

  /* Back */
  .back-mark {
    position: absolute;
    right: -70px; top: 120px;
    width: 330px; height: 330px;
    border-radius: 50%;
    background: var(--faint);
  }
  .back-lockup {
    position: absolute;
    left: 42px; top: 36px;
    display: flex;
    align-items: center;
    gap: 24px;
  }
  .back-lockup .brand-dot { width: 70px; height: 70px; }
  .back-lockup .brand-name { font-size: 40px; }

  .person {
    position: absolute;
    left: 42px; top: 148px;
  }
  .person-name {
    font-family: "Saira Semi Condensed", Arial, sans-serif;
    font-weight: 600;
    color: var(--gold);
    font-size: 22px;
    line-height: 1.1;
  }
  .person-title {
    color: var(--white);
    font-size: 15px;
    margin-top: 2px;
  }
  .rule {
    position: absolute;
    left: 42px; top: 206px;
    width: 560px; height: 2px;
    background: linear-gradient(90deg, var(--gold), var(--gold-deep));
  }
  .contact-list {
    position: absolute;
    left: 42px; top: 226px;
    list-style: none;
  }
  .contact-list li {
    display: flex;
    align-items: center;
    gap: 12px;
    color: var(--white);
    font-size: 16px;
    line-height: 1.6;
  }
  .contact-list svg { width: 14px; height: 14px; fill: var(--gold); }
  .address {
    position: absolute;
    right: 38px; bottom: 30px;
    text-align: right;
    color: var(--white);
    font-size: 17px;
    line-height: 1.4;
  }
</style>
</head>
<body>
  <section class="card card--front">
    <div class="front-lockup">
      <div class="brand-dot"></div>
      <div class="brand-name">VELMONT ARC</div>
    </div>
  </section>

  <section class="card card--back">
    <div class="back-mark"></div>
    <div class="back-lockup">
      <div class="brand-dot"></div>
      <div class="brand-name">VELMONT ARC</div>
    </div>
    <div class="person">
      <div class="person-name">Arden Vale Morrow</div>
      <div class="person-title">Managing Director</div>
    </div>
    <div class="rule"></div>
    <ul class="contact-list">
      <li>
        <svg viewBox="0 0 24 24" aria-hidden="true"><path d="M6.6 10.8a15.1 15.1 0 0 0 6.6 6.6l2.2-2.2a1 1 0 0 1 1-.25 11.4 11.4 0 0 0 3.6.57 1 1 0 0 1 1 1V20a1 1 0 0 1-1 1A17 17 0 0 1 3 4a1 1 0 0 1 1-1h3.5a1 1 0 0 1 1 1c0 1.25.2 2.45.57 3.6a1 1 0 0 1-.25 1z"/></svg>
        828-555-0192
      </li>
      <li>
        <svg viewBox="0 0 24 24" aria-hidden="true"><path d="M2 5h20v14H2zM4 7v.5l8 5 8-5V7l-8 5z"/></svg>
        arden@morrowmail.net
      </li>
    </ul>
    <div class="address">517 Harbor Ln., Fenwick,<br>Lakeview, US 204518</div>
  </section>
</body>
</html>
```